Veltrano.co - Polar Expeditions Specialists

We need a modern, visually striking business card for Veltrano.co, a company specialized in selling expedition cruises to the most remote regions on Earth, with a focus on the Arctic and Antarctica. The design should instantly communicate that the cardholder is an expert in polar travel. Use clean, premium aesthetics with cool tones like icy blue and white, possibly incorporating polar imagery (ice, glaciers, penguins, etc.)

Attached the logo

Contact Information for Business Card

Feels high-end and trustworthy.. Visually memorable — encourages people to keep it

Colors
0054AA
0677BA
7BADD7
CADEEF
E8F1F8

Requirements
Must have
• ice, glaciers, penguins, montains
Nice to have
• modern, transparente,

```html
<!DOCTYPE html>
<html lang="en">
<head>
<meta charset="utf-8">
<title>Veltrano.co – Business Card</title>
<link rel="stylesheet" href="https://fonts.googleapis.com/css2?family=Montserrat:wght@300;400;700;800&display=swap">
<style>
  :root{
    --deep-blue:#0054AA;
    --brand-blue:#2C77BA;
    --sky-blue:#7BADD7;
    --ice-blue:#CADEEF;
    --frost:#E8F1F8;
    --white:#ffffff;
    --ink:#2a2a2a;
    --backdrop:#e4e4e6;
  }
  *{box-sizing:border-box;margin:0;padding:0}
  html,body{width:1200px;height:900px;overflow:hidden}
  body{
    background:var(--backdrop);
    font-family:"Montserrat",sans-serif;
    position:relative;
  }
  .card{
    position:absolute;
    left:250px;
    width:700px;
    height:400px;
    border-radius:26px;
    overflow:hidden;
    box-shadow:0 6px 16px rgba(0,0,0,.18);
  }
  /* Front */
  .card-front{top:40px;background:var(--brand-blue)}
  .front-photo{
    position:absolute;inset:0;
    background:
      radial-gradient(ellipse 38% 46% at 55% 52%, rgba(232,241,248,.55), rgba(232,241,248,0) 70%),
      linear-gradient(180deg,#5c95cc 0%,#5a90c6 55%,#6b9fd0 100%);
  }
  .front-brand{
    position:absolute;left:50%;top:50%;
    transform:translate(-38%,-50%);
    color:var(--white);
  }
  .brand-row{display:flex;align-items:center;gap:14px}
  .brand-dot{width:26px;height:26px;border-radius:50%;background:var(--white)}
  .brand-name{font-weight:800;font-size:62px;letter-spacing:1px;line-height:1}
  .brand-tagline{font-weight:700;font-size:17px;margin-top:8px;margin-left:40px;letter-spacing:.3px}

  /* Back */
  .card-back{top:460px;background:var(--white)}
  .name-band{
    position:absolute;left:0;top:150px;
    width:420px;height:78px;
    background:var(--brand-blue);
    clip-path:polygon(0 0,100% 0,93% 100%,0 100%);
    color:var(--white);
    padding:12px 0 0 44px;
  }
  .holder-name{font-weight:800;font-size:30px;letter-spacing:1.5px;line-height:1.05}
  .holder-role{font-weight:300;font-size:20px;letter-spacing:.8px}
  .back-brand{
    position:absolute;left:440px;top:80px;color:var(--brand-blue);
  }
  .back-brand .brand-dot{width:18px;height:18px;background:var(--brand-blue)}
  .back-brand .brand-row{gap:9px}
  .back-brand .brand-name{font-size:36px}
  .back-brand .brand-tagline{font-size:10.5px;margin:4px 0 0 28px}
  .contact{
    position:absolute;left:110px;top:262px;color:var(--ink);
    font-weight:400;font-size:17px;letter-spacing:.8px;line-height:1.3;
  }
  .contact-address{margin-bottom:12px}
  .contact-list{list-style:none}
  .contact-list li{display:flex;align-items:center;gap:10px}
  .contact-icon{width:14px;height:14px;flex:none}
</style>
</head>
<body>
  <section class="card card-front" aria-label="Card front">
    <div class="front-photo" role="img" aria-label="Photo of a polar bear on snow under a blue tint"></div>
    <div class="front-brand">
      <div class="brand-row">
        <span class="brand-dot"></span>
        <span class="brand-name">Veltrano.co</span>
      </div>
      <div class="brand-tagline">Polar Expeditions Specialists</div>
    </div>
  </section>

  <section class="card card-back" aria-label="Card back">
    <div class="back-brand">
      <div class="brand-row">
        <span class="brand-dot"></span>
        <span class="brand-name">Veltrano.co</span>
      </div>
      <div class="brand-tagline">Polar Expeditions Specialists</div>
    </div>

    <div class="name-band">
      <div class="holder-name">MARCUS HALE</div>
      <div class="holder-role">CEO / Founder</div>
    </div>

    <div class="contact">
      <p class="contact-address">P.O. Box 3190 Harbour Lane<br>Norland City NV 4172</p>
      <ul class="contact-list">
        <li>
          <svg class="contact-icon" viewBox="0 0 16 16" aria-hidden="true"><path fill="#2C77BA" d="M3 1l3 3-1.5 2a9 9 0 0 0 5.5 5.5L12 10l3 3-2 2C7 15 1 9 1 3z"/></svg>
          +43 612 48 30 917
        </li>
        <li>
          <svg class="contact-icon" viewBox="0 0 16 16" aria-hidden="true"><rect x="1" y="3" width="14" height="10" rx="1" fill="#2C77BA"/><path d="M1.5 4l6.5 5 6.5-5" stroke="#fff" stroke-width="1.3" fill="none"/></svg>
          marcus.hale@veltrano.co
        </li>
        <li>
          <svg class="contact-icon" viewBox="0 0 16 16" aria-hidden="true"><circle cx="8" cy="8" r="7" fill="#2C77BA"/><path d="M1 8h14M8 1c3 3 3 11 0 14M8 1c-3 3-3 11 0 14" stroke="#fff" stroke-width="1" fill="none"/></svg>
          www.veltrano.co
        </li>
      </ul>
    </div>
  </section>
</body>
</html>
```